furniture and home contents restoration

I need to list the services that we perform in our studio.
we serve the general public as well as the insurance/ remediation industry

```html
<!DOCTYPE html>
<html lang="en">
<head>
<meta charset="UTF-8">
<title>Keystone Refinishers – Business Card</title>
<link rel="stylesheet" href="https://fonts.googleapis.com/css2?family=PT+Serif:wght@400;700&display=swap">
<style>
  :root {
    --bg: #2b2b2d;
    --ink: #1c3039;
    --card-dark: #213941;
    --card-light: #ffffff;
    --strip-light: #c9c9cb;
    --on-dark: #ffffff;
  }
  * { margin: 0; padding: 0; box-sizing: border-box; }
  html, body {
    width: 1200px; height: 900px; overflow: hidden;
    background: var(--bg);
    font-family: "PT Serif", Georgia, serif;
    text-transform: uppercase;
  }
  .card {
    position: absolute; left: 250px; width: 700px; height: 400px;
    border-radius: 18px; overflow: hidden;
  }
  /* Back side */
  .card-back { top: 25px; background: var(--card-dark); color: var(--on-dark); }
  .card-back .brand {
    position: absolute; top: 22px; width: 100%; text-align: center;
    font-size: 34px; font-weight: 700; letter-spacing: 1px;
  }
  .service-list {
    position: absolute; list-style: none; font-size: 12.5px; line-height: 17px;
  }
  .service-list li::before { content: "• "; }
  .service-list.left { left: 48px; top: 82px; }
  .service-list.right { left: 372px; top: 120px; }
  .card-back .offer {
    position: absolute; left: 0; width: 100%; text-align: center;
    font-size: 16px; line-height: 22px;
  }
  .offer.first { top: 322px; }
  .offer.second { top: 344px; }

  /* Front side */
  .card-front { top: 475px; background: var(--card-light); color: var(--ink); }
  .card-front .brand {
    position: absolute; left: 40px; top: 28px;
    font-size: 44px; line-height: 46px; font-weight: 700;
  }
  .tagline-top {
    position: absolute; right: 40px; top: 78px;
    font-size: 16px; font-weight: 700; letter-spacing: .5px;
  }
  .contact { position: absolute; left: 40px; top: 228px; font-size: 15px; line-height: 22px; }
  .contact .person { font-size: 24px; font-weight: 700; line-height: 30px; margin-bottom: 2px; }
  .contact b { display: inline-block; width: 16px; }
  .tagline-bottom {
    position: absolute; right: 40px; bottom: 46px; text-align: right;
    font-size: 17px; line-height: 24px;
  }
  .edge-strip { position: absolute; left: 0; bottom: 0; width: 700px; height: 14px; }
</style>
</head>
<body>
  <section class="card card-back">
    <h1 class="brand">Keystone Refinishers</h1>
    <ul class="service-list left">
      <li>Antique repair and restoration</li>
      <li>Art cleaning and remounting</li>
      <li>Art and mirror frame repair</li>
      <li>Chandelier cleaning and restoration</li>
      <li>Document restoration</li>
      <li>Glass, ceramic, and mirror repair</li>
      <li>Hardware repair and restoration</li>
      <li>Kitchen removal and reinstallation</li>
      <li>Lamp cleaning and restoration</li>
      <li>Lamp shade replacement</li>
    </ul>
    <ul class="service-list right">
      <li>Metal polishing and restoration</li>
      <li>Odor removal and ozone services</li>
      <li>Photo restoration</li>
      <li>Upholstery cleaning and deodorizing</li>
      <li>In-house upholstery and reupholstery</li>
      <li>Rug cleaning and restoration</li>
      <li>Musical instrument restoration</li>
      <li>Window treatment repair/ restoration</li>
      <li>Leather restoration and replacement</li>
      <li>Piano restoration and repair</li>
    </ul>
    <p class="offer first">On-site inspections and desk review services</p>
    <p class="offer second">Assessment reports and estimates for repair and restoration</p>
  </section>

  <section class="card card-front">
    <h1 class="brand">Keystone<br>Refinishers</h1>
    <p class="tagline-top">Home contents restoration</p>
    <div class="contact">
      <p class="person">Daniel Moretti</p>
      <p><b>O</b> -555.201.4400</p>
      <p><b>M</b> -555.308.6120</p>
      <p><b>F</b> -555.201.4460</p>
      <p>18 Alder Brook Rd. Millford, NY 10500</p>
      <p>info@keystonerefin.com</p>
    </div>
    <p class="tagline-bottom">Serving the general public<br>and the insurance industry<br>for over 40 years</p>
    <svg class="edge-strip" viewBox="0 0 700 14" aria-hidden="true">
      <polygon points="0,0 390,0 380,14 0,14" fill="var(--strip-light)"/>
      <polygon points="390,0 700,0 700,14 380,14" fill="var(--card-dark)"/>
    </svg>
  </section>
</body>
</html>
```